Heron Loan Partners Business Card

We need a business card design for our mortgage servicing company. In addition to servicing the loans of homeowners, we help homeowners with purchasing their homes and any mortgage refinancing. We would like to see designs that use the colors in the logo attached below (gold-ish yellow and navy blue), and any other design you deem fit! The design should communicate a Easy living with clever home loans provided by Heron.

```html
<!DOCTYPE html>
<html lang="en">
<head>
<meta charset="utf-8">
<title>Heron Loan Partners – Business Card</title>
<link href="https://fonts.googleapis.com/css2?family=Arimo:wght@400;700&display=swap" rel="stylesheet">
<style>
  :root {
    --gold: #c9a22f;
    --navy: #221d55;
    --paper: #f5f5f3;
    --backdrop: #2a2a2c;
    --white: #ffffff;
  }
  * { margin: 0; padding: 0; box-sizing: border-box; }
  html, body { width: 1200px; height: 874px; overflow: hidden; }
  body {
    background: var(--backdrop);
    font-family: "Arimo", Arial, sans-serif;
    display: flex;
    align-items: center;
    justify-content: center;
    gap: 40px;
  }
  .card {
    position: relative;
    width: 540px;
    height: 309px;
    border-radius: 16px;
    overflow: hidden;
    box-shadow: 0 10px 28px rgba(0,0,0,.45);
  }
  /* Front */
  .card-front {
    background: var(--gold);
    display: flex;
    flex-direction: column;
    align-items: center;
    justify-content: center;
  }
  .front-brand {
    font-weight: 700;
    font-size: 44px;
    color: var(--navy);
    letter-spacing: .5px;
    display: flex;
    align-items: center;
    gap: 14px;
  }
  .brand-dot {
    width: 16px; height: 16px; border-radius: 50%;
    background: var(--navy);
  }
  .front-web {
    margin-top: 52px;
    font-size: 14px;
    letter-spacing: 4px;
    color: var(--navy);
  }
  /* Back */
  .card-back { background: var(--paper); }
  .back-brand {
    position: absolute;
    left: 34px; top: 40px;
    font-weight: 700;
    font-size: 28px;
    color: var(--gold);
  }
  .holder {
    position: absolute;
    right: 34px; top: 80px;
    text-align: right;
  }
  .holder-name { font-weight: 700; font-size: 22px; color: var(--gold); }
  .holder-role { font-size: 15px; color: var(--navy); margin-top: 3px; }
  .wave { position: absolute; left: 0; top: 0; width: 540px; height: 309px; }
  .contacts {
    position: absolute;
    right: 34px; top: 184px;
    text-align: right;
    color: var(--white);
    font-size: 14px;
    line-height: 18px;
  }
  .contact-line { display: flex; align-items: center; justify-content: flex-end; gap: 7px; }
  .contact-line svg { width: 11px; height: 11px; flex: none; }
  .address { padding-right: 18px; }
  .tagline { margin-top: 4px; padding-right: 18px; }
</style>
</head>
<body>
  <section class="card card-front">
    <div class="front-brand"><span class="brand-dot"></span>Heron Loan Partners</div>
    <div class="front-web">www.Heron.com</div>
  </section>

  <section class="card card-back">
    <svg class="wave" viewBox="0 0 540 309" aria-hidden="true">
      <path d="M0,178 C140,222 310,140 540,134 L540,142 C320,150 150,232 0,190 Z" fill="var(--gold)"/>
      <path d="M0,206 C130,246 310,162 540,156 L540,309 L0,309 Z" fill="var(--navy)"/>
    </svg>
    <div class="back-brand">Heron Loan Partners</div>
    <div class="holder">
      <div class="holder-name">Nathan Cole</div>
      <div class="holder-role">President</div>
    </div>
    <div class="contacts">
      <div class="contact-line">(555) 0142-7781
        <svg viewBox="0 0 12 12"><path d="M2.5 1 L4.5 1 L5.3 3.6 L4 4.6 C4.7 6.1 5.9 7.3 7.4 8 L8.4 6.7 L11 7.5 L11 9.5 C11 10.3 10.3 11 9.5 11 C5 11 1 7 1 2.5 C1 1.7 1.7 1 2.5 1 Z" fill="var(--gold)"/></svg>
      </div>
      <div class="contact-line">name@Heron.com
        <svg viewBox="0 0 12 12"><rect x="0.5" y="2" width="11" height="8" fill="var(--gold)"/><path d="M0.5 2 L6 6.5 L11.5 2" stroke="var(--navy)" stroke-width="1" fill="none"/></svg>
      </div>
      <div class="contact-line">www.Heron.com
        <svg viewBox="0 0 12 12"><circle cx="6" cy="6" r="5.5" fill="var(--gold)"/><path d="M0.5 6 H11.5 M6 0.5 C3 3 3 9 6 11.5 M6 0.5 C9 3 9 9 6 11.5" stroke="var(--navy)" stroke-width=".8" fill="none"/></svg>
      </div>
      <div class="address">4127 Willowbank Road<br>Cedar Hollow, NY 11920</div>
      <div class="tagline">Easy living with clever home loans</div>
    </div>
  </section>
</body>
</html>
```